Birch Hauling Business Card Design Project

We need a new company business card. We provide professional timber harvesting (logging) and forest management services. I'm open to any creative design. Most company caps and shirts are navy blue and Light grey. Logo does not necessarily have to contain those colors. Logo containing picture of logging equipment, log truck, trees, or logs are acceptable. Be creative. Final logo should communicate our company's pride and professionalism in the East Texas Timber Industry.
Updates

Target Market(s)

Timber owners, sawmills, and forestry professionals

Industry/Entity Type

Business

Requirements
Must have
• Must have Contact Info.
Phone: 936-402-5917
address: PO Box 4830
New Waverly, Tx 77358
www.jmbirchhauling.example
jmbirchhauling@mailbox.example
Owner: Jared Marsh

Or design must leave room for this info.

```html
<!DOCTYPE html>
<html lang="en">
<head>
<meta charset="utf-8">
<title>Birch Hauling – Business Card</title>
<link rel="stylesheet" href="https://fonts.googleapis.com/css2?family=Michroma&display=swap">
<style>
  :root {
    --page: #e9e9e9;
    --card-top: #ffffff;
    --card-mid: #eeeeee;
    --red: #e42f36;
    --red-deep: #c9232b;
    --charcoal: #333335;
    --ink: #3a3a3c;
    --white: #ffffff;
  }
  * { box-sizing: border-box; margin: 0; padding: 0; }
  html, body { width: 1200px; height: 900px; overflow: hidden; }
  body {
    background: var(--page);
    display: flex; align-items: center; justify-content: center;
    font-family: "Michroma", "Helvetica Neue", Arial, sans-serif;
  }
  .card {
    position: relative;
    width: 1050px; height: 600px;
    border-radius: 44px;
    overflow: hidden;
    background: radial-gradient(ellipse at 60% 35%, var(--card-top) 0%, var(--card-mid) 80%);
    box-shadow: 0 10px 30px rgba(0,0,0,0.18);
  }
  .card__wave { position: absolute; inset: 0; width: 100%; height: 100%; }
  .brand {
    position: absolute; left: 80px; top: 70px;
    display: flex; align-items: center; gap: 20px;
  }
  .brand__square { width: 26px; height: 26px; background: var(--red); }
  .brand__name {
    color: var(--charcoal);
    font-size: 30px; line-height: 1.25;
    text-transform: uppercase; letter-spacing: 1px;
  }
  .owner {
    position: absolute; left: 80px; top: 222px;
    color: var(--ink);
    font-variant: small-caps;
    letter-spacing: 3px;
  }
  .owner__name { font-size: 28px; }
  .owner__title { font-size: 21px; margin-top: 10px; }
  .contact {
    position: absolute; left: 560px; top: 402px;
    list-style: none;
    color: var(--white);
    font-size: 14px; letter-spacing: 0.8px;
    white-space: nowrap;
  }
  .contact__item { display: flex; align-items: flex-start; gap: 12px; margin-bottom: 8px; line-height: 1.4; }
  .contact__item:last-child { margin-bottom: 0; }
  .contact__icon { flex: none; width: 18px; height: 18px; margin-top: 1px; }
</style>
</head>
<body>
  <div class="card">
    <svg class="card__wave" viewBox="0 0 1050 600" preserveAspectRatio="none" aria-hidden="true">
      <defs>
        <linearGradient id="redFill" x1="0" y1="0" x2="1" y2="1">
          <stop offset="0" stop-color="#c9232b"/>
          <stop offset="1" stop-color="#ec343b"/>
        </linearGradient>
      </defs>
      <path d="M0,268 C260,420 640,420 1050,196" fill="none" stroke="#333335" stroke-width="9"/>
      <path d="M0,290 C260,442 640,442 1050,218 L1050,600 L0,600 Z" fill="url(#redFill)"/>
    </svg>

    <div class="brand">
      <span class="brand__square"></span>
      <p class="brand__name">Jared Marsh<br>Birch Hauling</p>
    </div>

    <div class="owner">
      <p class="owner__name">Jared Marsh</p>
      <p class="owner__title">Owner / C.E.O</p>
    </div>

    <ul class="contact">
      <li class="contact__item">
        <svg class="contact__icon" viewBox="0 0 20 20"><circle cx="10" cy="10" r="10" fill="#fff"/><path d="M10 4a4 4 0 0 0-4 4c0 3 4 8 4 8s4-5 4-8a4 4 0 0 0-4-4z" fill="#e42f36"/><circle cx="10" cy="8" r="1.5" fill="#fff"/></svg>
        <span>PO Box 4830,<br>New Waverly, TX 77358</span>
      </li>
      <li class="contact__item">
        <svg class="contact__icon" viewBox="0 0 20 20"><circle cx="10" cy="10" r="10" fill="#fff"/><path d="M6 5h3l1 3-2 1a7 7 0 0 0 3 3l1-2 3 1v3c-5 1-10-4-9-9z" fill="#e42f36"/></svg>
        <span>936-402-5917</span>
      </li>
      <li class="contact__item">
        <svg class="contact__icon" viewBox="0 0 20 20"><circle cx="10" cy="10" r="10" fill="#fff"/><rect x="7" y="4" width="6" height="12" rx="1" fill="#e42f36"/></svg>
        <span>936-402-5918</span>
      </li>
      <li class="contact__item">
        <svg class="contact__icon" viewBox="0 0 20 20"><circle cx="10" cy="10" r="10" fill="#fff"/><rect x="5" y="8" width="10" height="7" fill="#e42f36"/><rect x="7" y="4" width="6" height="4" fill="#e42f36"/></svg>
        <span>936-402-5919</span>
      </li>
      <li class="contact__item">
        <svg class="contact__icon" viewBox="0 0 20 20"><circle cx="10" cy="10" r="10" fill="#fff"/><rect x="4.5" y="6" width="11" height="8" fill="#e42f36"/><path d="M4.5 6l5.5 4.5L15.5 6" fill="none" stroke="#fff" stroke-width="1.2"/></svg>
        <span>jmbirchhauling@mailbox.example</span>
      </li>
      <li class="contact__item">
        <svg class="contact__icon" viewBox="0 0 20 20"><circle cx="10" cy="10" r="10" fill="#fff"/><circle cx="10" cy="10" r="5.5" fill="none" stroke="#e42f36" stroke-width="1.4"/><path d="M4.5 10h11M10 4.5c-3 3-3 8 0 11M10 4.5c3 3 3 8 0 11" fill="none" stroke="#e42f36" stroke-width="1.2"/></svg>
        <span>www.jmbirchhauling.example</span>
      </li>
    </ul>
  </div>
</body>
</html>
```